Retail Package for Ammunition Company

We are looking for a packaging design for a retail boxed ammunition. The "look". Attached will be the logo to be used. The logo is attached and a can be manipulated on the box. Box to represent strength and accuracy. Will need to provide .psd files to allow in house personnel to add/remove text to other calibers and warnings. Wow me with your designs!

Browse Other Brands: http://www.brightfalconsupply.com/brands

The packaging needs to include:
Logo- provided and the following text:

FRONT 1. 9mm 115gr FMJ

BACK 2. WARNING: To avoid serious injury: (1) use only ammunition in good condition; use only in modern firearms in good condition marked for .22 Long Rifle (LR) cartridges; (2) always be sure barrel is free of any obstructions; the barrel should be checked in case of light recoil, or an unusually loud or weak sound heard during firing; (3) wear eye and ear protection; (4) if gun fails to fire, avoid exposure to breech when unloading and point muzzle in a safe direction. Keep firearm pointed in safe direction at all times; (5) discharge may occur if rim is struck; handle with caution, do not drop. (6) Do not shoot at hard surfaces or water to prevent ricochet; (7) Bullet is capable of traveling extreme distances. Know your backstop; (8) Store in cool dry place

3. LEAD WARNING: Discharging firearms in poorly ventilated areas, cleaning firearms, or handling ammunition may result in exposure to lead and other substances known to cause birth defects, reproductive harm, and other serious physical injury. Have adequate ventilation at all times. Wash hands thoroughly after exposure.

Dimensions ; (LxWxH): 5.25" x 2.625" x 1.125"

Target Market(s)

Ammunition Industry

```html
<!DOCTYPE html>
<html lang="en">
<head>
<meta charset="utf-8">
<title>Volt Ammunition – 9MM 115GR FMJ Retail Box</title>
<link rel="stylesheet" href="https://fonts.googleapis.com/css2?family=Black+Ops+One&family=Cinzel:wght@700;900&family=Montserrat:wght@500;800&display=swap">
<style>
  :root {
    --navy: #1d1a4f;
    --red: #e8343c;
    --red-deep: #d8262e;
    --gold: #f2c21b;
    --white: #ffffff;
    --stage: #ececec;
  }
  * { box-sizing: border-box; margin: 0; padding: 0; }
  html, body {
    width: 1200px; height: 892px; overflow: hidden;
    background: var(--stage);
  }
  .dieline {
    position: absolute; left: 26px; top: 108px;
    width: 1148px; height: 676px;
  }
  .panel { position: absolute; overflow: hidden; }
  .brush-field { position: absolute; inset: 0; }

  /* Shared brand wordmark: one colour, one weight of the text font */
  .brand-mark {
    display: flex; align-items: center; gap: 12px;
  }
  .brand-dot {
    width: 26px; height: 26px; border-radius: 50%;
    background: var(--white); flex: none;
  }
  .brand-name {
    font-family: "Montserrat", sans-serif; font-weight: 800;
    font-size: 26px; color: var(--white); letter-spacing: 2px;
    line-height: 1.15; text-transform: uppercase;
  }

  /* Top panel */
  .panel-top {
    left: 0; top: 0; width: 945px; height: 473px;
  }
  .panel-top .brush-field {
    background: linear-gradient(118deg, var(--navy) 0%, var(--navy) 46%, #5a2450 54%, var(--red) 63%, var(--red) 100%);
  }
  .panel-top .brand-mark {
    position: absolute; left: 200px; top: 72px;
  }
  .top-grade {
    position: absolute; left: 96px; top: 250px;
    font-family: "Cinzel", serif; font-weight: 900;
    font-size: 96px; color: var(--white); letter-spacing: 14px; line-height: 1;
  }
  .top-product {
    position: absolute; left: 560px; top: 150px;
  }
  .product-name {
    font-family: "Black Ops One", sans-serif; color: var(--white);
    line-height: 0.9;
  }
  .product-line {
    font-family: "Black Ops One", sans-serif; color: var(--gold);
    line-height: 1;
  }
  .top-product .product-name { font-size: 104px; }
  .top-product .product-line { font-size: 40px; margin-left: 18px; }
  .top-calibre {
    position: absolute; left: 570px; top: 330px;
    font-family: "Cinzel", serif; font-weight: 900;
    font-size: 44px; color: var(--white); letter-spacing: 2px;
  }
  .top-url {
    position: absolute; left: 520px; top: 400px;
    font-family: "Montserrat", sans-serif; font-weight: 800;
    font-size: 24px; color: var(--white);
  }

  /* Front panel */
  .panel-front {
    left: 0; top: 473px; width: 945px; height: 203px;
  }
  .panel-front .brush-field {
    background: linear-gradient(100deg, var(--navy) 0%, var(--navy) 38%, #5a2450 46%, var(--red) 54%, var(--red) 100%);
  }
  .front-brand {
    position: absolute; left: 24px; top: 44px; width: 164px;
    flex-direction: column; gap: 10px;
  }
  .front-brand .brand-dot { width: 56px; height: 56px; }
  .front-brand .brand-name { font-size: 15px; letter-spacing: 1px; text-align: center; }
  .front-product { position: absolute; left: 206px; top: 38px; }
  .front-product .product-name { font-size: 96px; }
  .front-product .product-line { font-size: 36px; margin-left: 10px; }
  .front-spec {
    position: absolute; left: 570px; top: 36px;
    font-family: "Cinzel", serif; font-weight: 900; color: var(--white);
    line-height: 1;
  }
  .front-spec .spec-grade { font-size: 88px; letter-spacing: 10px; }
  .front-spec .spec-calibre { font-size: 46px; letter-spacing: 2px; margin-top: 6px; }

  /* End panel */
  .panel-end {
    left: 945px; top: 0; width: 203px; height: 473px;
    background: var(--red-deep);
  }
  .end-warnings {
    position: absolute; left: 50%; top: 50%;
    width: 440px;
    transform: translate(-50%, -50%) rotate(90deg);
    font-family: "Montserrat", sans-serif; font-weight: 500;
    font-size: 13px; line-height: 1.45; color: var(--white);
  }
  .end-warnings strong { font-weight: 800; }
  .end-warnings p + p { margin-top: 8px; }
</style>
</head>
<body>
  <main class="dieline">
    <section class="panel panel-top">
      <div class="brush-field" role="img" aria-label="Navy and red brush-stroke texture with halftone dots"></div>
      <div class="brand-mark">
        <span class="brand-dot"></span>
        <span class="brand-name">Northgate Cartridge Co.</span>
      </div>
      <div class="top-grade">FMJ</div>
      <div class="top-product">
        <div class="product-name">VOLT</div>
        <div class="product-line">AMMUNITION</div>
      </div>
      <div class="top-calibre">9MM 115GR</div>
      <div class="top-url">www.northgatecartridge.com</div>
    </section>

    <section class="panel panel-front">
      <div class="brush-field" role="img" aria-label="Navy and red brush-stroke texture with halftone dots"></div>
      <div class="brand-mark front-brand">
        <span class="brand-dot"></span>
        <span class="brand-name">Northgate</span>
      </div>
      <div class="front-product">
        <div class="product-name">VOLT</div>
        <div class="product-line">AMMUNITION</div>
      </div>
      <div class="front-spec">
        <div class="spec-grade">FMJ</div>
        <div class="spec-calibre">9MM 115GR</div>
      </div>
    </section>

    <section class="panel panel-end">
      <div class="end-warnings">
        <p><strong>WARNING:</strong> Use only in modern firearms in good condition chambered for this cartridge. Wear eye and ear protection. Know your backstop. Store in a cool, dry place.</p>
        <p><strong>LEAD WARNING:</strong> Handling ammunition may expose you to lead. Ensure good ventilation. Wash hands after use.</p>
      </div>
    </section>
  </main>
</body>
</html>
```